Redesign of Form/Document Navigation Page

I need a redesign of our document and navigation bar on the left. We want the same navigation bar layout/setup but want the buttons and typography to be simple and matching all over. The form needs to be aesthetically pleasing and fit within the page.

1st attachment is our Direct Deposit and the second is the form continued.

```html
<!DOCTYPE html>
<html lang="en">
<head>
<meta charset="utf-8">
<title>Direct Deposit Enrollment</title>
<link href="https://fonts.googleapis.com/css2?family=Lato:wght@300;400;700&display=swap" rel="stylesheet">
<style>
:root{
  --page:#f5f5f5;
  --white:#ffffff;
  --gold:#e3b448;
  --gold-text:#e9b62b;
  --blue:#2a56c6;
  --ink:#333333;
  --muted:#555555;
  --field:#f0f0f0;
  --box:#ededed;
  --radio:#cfcfcf;
  --pct:#fadd9a;
  --social:#c8c8c8;
}
*{box-sizing:border-box;margin:0;padding:0}
html,body{width:1200px;height:1037px;overflow:hidden}
body{background:var(--page);font-family:'Lato',sans-serif;color:var(--ink);position:relative}
.topbar{position:absolute;left:0;top:0;width:1200px;height:107px;background:var(--white)}
.brand{position:absolute;left:43px;top:24px;display:flex;align-items:center;gap:10px}
.brand-mark{width:48px;height:48px;border-radius:50%;background:var(--blue)}
.brand-name{font-weight:700;font-size:22px;line-height:22px;color:var(--gold-text);width:180px}
.nav{position:absolute;top:36px;right:55px;display:flex;align-items:center;height:36px}
.nav a{font-size:14px;text-decoration:none;color:var(--muted);display:flex;align-items:center;gap:6px;margin-right:30px}
.nav a.active{color:var(--blue)}
.nav .divider{width:1px;height:40px;background:#ddd;margin-right:20px}
.nav .user{font-size:14px;color:var(--ink);margin-right:19px}
.power{width:35px;height:35px;background:var(--blue);display:flex;align-items:center;justify-content:center}
.back{position:absolute;left:43px;top:119px;font-size:12.5px;color:var(--muted);display:flex;align-items:center;gap:6px}
.sidebar{position:absolute;left:43px;top:145px;width:294px}
.side-item{height:87px;background:var(--white);margin-bottom:7.3px;position:relative;display:flex;align-items:center}
.side-item .tab{position:absolute;left:12px;top:12px;width:62px;height:65px;background:var(--gold)}
.side-item .dot{position:absolute;left:50px;top:20px;width:47px;height:47px;border-radius:50%;background:var(--blue);border:2px solid var(--white);display:flex;align-items:center;justify-content:center}
.side-item .label{margin-left:107px;font-size:14px;color:var(--ink);position:relative;top:-5px}
.panel{position:absolute;left:351px;top:145px;width:807px;height:774px;background:var(--white);padding:0 17px}
.panel h1{font-weight:400;font-size:27px;text-align:center;margin-top:33px;color:var(--ink)}
.intro{font-weight:300;font-size:13.3px;line-height:17.2px;text-align:center;color:var(--ink);margin:22px 2px 0}
.attach{margin-top:20px;height:91px;background:var(--box);display:flex;align-items:center;justify-content:center;gap:30px;font-weight:300;font-size:14.5px}
.btn{background:var(--blue);color:var(--white);font-size:14px;width:114px;height:33px;display:flex;align-items:center;justify-content:center;font-weight:300}
.panel h2{font-weight:400;font-size:17px;margin-top:31px}
.note{font-weight:300;font-size:12.5px;line-height:17px}
.note.first{margin-top:6px;margin-bottom:4px}
.radios{display:flex;gap:28px;margin-top:14px;font-size:13px;font-weight:400}
.radio{display:flex;align-items:center;gap:9px}
.radio i{width:8px;height:8px;border-radius:50%;background:var(--radio);display:block}
.row{display:flex;gap:12px;margin-top:31px}
.row.second{margin-top:20px}
.field label{display:block;font-weight:300;font-size:13px;margin-bottom:9px}
.field .input{height:29px;background:var(--field)}
.acct{display:flex;align-items:center;margin-top:21px;font-size:13.5px;font-weight:300}
.acct .radio{margin-right:28px}
.acct .pct{width:84px;height:28px;background:var(--pct);display:flex;align-items:center;padding-left:9px;font-size:12px;margin:0 8px 0 18px}
.important{font-weight:400;font-size:13px;margin-top:30px}
.legal{font-weight:300;font-size:11.2px;line-height:15.5px;margin-top:12px;color:var(--ink)}
.footer{position:absolute;left:0;top:962px;width:1200px;height:75px;background:var(--white)}
.footer .copy{position:absolute;left:44px;top:32px;font-size:12.5px;color:var(--muted);font-weight:300}
.social{position:absolute;right:42px;top:18px;display:flex;gap:8px}
.social span{width:37px;height:37px;border-radius:50%;background:var(--social);display:block}
</style>
</head>
<body>
<header class="topbar">
  <div class="brand"><span class="brand-mark"></span><span class="brand-name">NORTHGATE PATROL SERVICES</span></div>
  <nav class="nav">
    <a class="active" href="#"><svg width="12" height="11" viewBox="0 0 12 11"><path d="M6 0 0 5h2v6h3V7h2v4h3V5h2z" fill="#2a56c6"/></svg>Home</a>
    <a href="#"><b>?</b> Help</a>
    <span class="divider"></span>
    <span class="user">Dana Rivers</span>
    <span class="power"><svg width="20" height="20" viewBox="0 0 20 20" fill="none" stroke="#fff" stroke-width="2.2" stroke-linecap="round"><path d="M6 4.5a7.5 7.5 0 1 0 8 0"/><path d="M10 1.5v8"/></svg></span>
  </nav>
</header>

<div class="back"><svg width="12" height="12" viewBox="0 0 12 12" fill="none" stroke="#555" stroke-width="2"><path d="M10 6a4 4 0 1 1-1.2-2.8"/><path d="M10 1v3H7" stroke-width="1.6"/></svg>Back To Profile</div>

<aside class="sidebar">
  <div class="side-item"><span class="tab"></span><span class="dot"><svg width="16" height="11"><rect x="1" y="1" width="14" height="9" fill="none" stroke="#fff" stroke-width="2"/><circle cx="8" cy="5.5" r="2" fill="#fff"/></svg></span><span class="label">Direct Deposit</span></div>
  <div class="side-item"><span class="tab"></span><span class="dot"><svg width="16" height="11"><rect x="1" y="1" width="14" height="9" fill="none" stroke="#fff" stroke-width="2"/><circle cx="8" cy="5.5" r="2" fill="#fff"/></svg></span><span class="label">Change W-4</span></div>
  <div class="side-item"><span class="tab"></span><span class="dot"><svg width="14" height="12" fill="#fff"><rect x="0" y="0" width="2" height="2"/><rect x="4" y="0" width="10" height="2"/><rect x="0" y="5" width="2" height="2"/><rect x="4" y="5" width="10" height="2"/><rect x="0" y="10" width="2" height="2"/><rect x="4" y="10" width="10" height="2"/></svg></span><span class="label">Labour Code</span></div>
  <div class="side-item"><span class="tab"></span><span class="dot"><svg width="12" height="12" fill="#fff"><circle cx="6" cy="3.5" r="3"/><path d="M0 12a6 5 0 0 1 12 0z"/></svg></span><span class="label">Personal Information</span></div>
  <div class="side-item"><span class="tab"></span><span class="dot"><svg width="13" height="13" fill="#fff"><path d="M9 1l3 3-7 7H2V8z"/></svg></span><span class="label">Appraisal and Review</span></div>
  <div class="side-item"><span class="tab"></span><span class="dot"><svg width="12" height="14" fill="none" stroke="#fff" stroke-width="1.5"><path d="M1 1h7l3 3v9H1z"/><path d="M3.5 7h5M3.5 10h5"/></svg></span><span class="label">Write Up-Slip</span></div>
  <div class="side-item"><span class="tab"></span><span class="dot"><svg width="16" height="12" fill="#fff"><path d="M1 0v11h15v1H0V0z"/><path d="M2 10l3-5 3 3 3-6 4 8z"/></svg></span><span class="label">Employee Performance</span></div>
</aside>

<main class="panel">
  <h1>Employee Direct Deposit Enrollment Form</h1>
  <p class="intro">To enroll in Direct Deposit, simply fill out this form. Attach a voided check for each checking account - not a deposit slip. If depositing to a savings account, ask your bank to give you the Routing/Transit Number for your account. It isn't always the same as the number on a savings deposit slip. This will help ensure that you are paid correctly. Once filled out, accounting will review your information for processing. Once processed, you will receive an email confirmation with details. Employees must attach a voided check for each of their accounts to help verify their account numbers and bank routing numbers.</p>
  <div class="attach"><span>Attach A Voided Check Or Bank Deposit Form for the Account</span><span class="btn">REFRESH</span></div>
  <h2>Account Information</h2>
  <p class="note first">The last item must be for the remaining amount owed to you. To distribute to more accounts, please complete another form.</p>
  <p class="note" style="font-weight:400">Make sure to indicate what kind of account, along with enrolling or declining<br>**NOTIFY PAYROLL IMMEDIATELY IF YOU CLOSE OR CHANGE BANK ACCOUNT**</p>
  <div class="radios">
    <span class="radio"><i></i>New Enrollment</span>
    <span class="radio"><i></i>Change Enrollment</span>
    <span class="radio"><i></i>Cancel Enrollment</span>
  </div>
  <div class="row">
    <div class="field" style="width:250px"><label>Bank Name:</label><div class="input"></div></div>
    <div class="field" style="width:250px"><label>City:</label><div class="input"></div></div>
    <div class="field" style="width:250px"><label>State:</label><div class="input"></div></div>
  </div>
  <div class="row second">
    <div class="field" style="width:382px"><label>Routing Transit#:</label><div class="input"></div></div>
    <div class="field" style="width:380px"><label>Account Number:</label><div class="input"></div></div>
  </div>
  <div class="acct">
    <span class="radio"><i></i>Checking</span>
    <span class="radio"><i></i>Saving</span>
    <span style="margin-left:18px">Account :</span>
    <span class="pct">100</span>
    <span>%</span>
  </div>
  <p class="important">IMPORTANT! Please read and sign before completing and submitting</p>
  <p class="legal">I hereby authorize NORTHGATE PATROL SERVICES to deposit any amounts owed me, as instructed by my employer, by initiating credit entries to my account at the financial institution (hereinafter "Bank") indicated on this form. Further, I authorize Bank to accept and to credit any credit entries indicated by NORTHGATE PATROL SERVICES to my account. In the event that NORTHGATE PATROL SERVICES deposits funds erroneously into my account, I authorize NORTHGATE PATROL SERVICES to</p>
</main>

<footer class="footer">
  <p class="copy">Copyright(c) 2016 website name, All Rights Reserved.</p>
  <div class="social"><span></span><span></span><span></span></div>
</footer>
</body>
</html>
```